Business Card Design For Office Furniture Clearance Company

Kestrel Office Clearance - our company name pretty much explains what we do, we clear offices for high end clients, mainly plc's and large international companies.

We require a nice looking business card that displays professionalism but without being too serious.

It would be nice to see just a little more than a conventional boring business card, make sure you add some flare.

Industry/Entity Type

Office Furniture

Contact Information for Business Card

CARD 1

Mark Holloway
Director
mark@kestrelofficeclearance.co.uk
m: 07700 153928

t: 01632 960418
www.kestrelofficeclearance.co.uk

Kestrel Office Clearance
Unit K4 B
2-8 Fenwick Lane
Ashcombe
Northfield Vale
ZZ9 4QT

free office clearances… you cant get better than that.

CARD 2

Peter Radford
Director
peter@kestrelofficeclearance.co.uk
m: 07700 382615

t: 01632 960418

Kestrel Office Clearance
Unit K4 B
2-8 Fenwick Lane
Ashcombe
Northfield Vale
ZZ9 4QT

Font styles to use
Sans Serif

Requirements
Must have
• A white background - as we have a blue logo.
Nice to have
• Nice use of the logo - play around with this and dissect it.

```html
<!DOCTYPE html>
<html lang="en">
<head>
<meta charset="utf-8">
<title>Kestrel Office Clearance – Business Card</title>
<link rel="stylesheet" href="https://fonts.googleapis.com/css2?family=Open+Sans:ital,wght@0,400;0,600;1,400&display=swap">
<style>
:root{
  --stage:#e8ebee;
  --card:#ffffff;
  --brand:#2b8fd6;
  --brand-deep:#1a72b8;
  --brand-light:#4aa8e6;
  --brand-mist:#e4f0fa;
  --ink:#555a60;
  --ink-soft:#7b8086;
  --rule:#d5d9dd;
}
*{margin:0;padding:0;box-sizing:border-box}
html,body{width:1200px;height:950px;overflow:hidden}
body{
  background:var(--stage);
  font-family:"Open Sans",Arial,sans-serif;
  display:flex;flex-direction:column;align-items:center;justify-content:center;gap:70px;
}
.card{
  position:relative;width:560px;height:320px;background:var(--card);
  box-shadow:0 6px 18px rgba(0,0,0,.14);overflow:hidden;
}
/* front */
.brand-disc{
  position:absolute;left:38px;top:44px;width:190px;height:190px;border-radius:50%;
  background:linear-gradient(135deg,var(--brand-light),var(--brand-deep));
}
.details{position:absolute;left:262px;top:34px;right:24px;color:var(--ink)}
.person-name{font-size:25px;font-weight:600;color:var(--brand);line-height:1.1}
.person-role{font-size:14px;margin-top:2px}
.divider{height:1px;background:var(--rule);margin:10px 0 9px}
.company-name{font-size:14px;font-weight:600;color:var(--brand)}
.address{font-size:12.5px;line-height:1.45;font-style:normal}
.contact{list-style:none;margin-top:8px;font-size:12.5px;line-height:1.55}
.contact li{display:flex;align-items:center;gap:7px}
.contact svg{width:12px;height:12px;flex:none}
.web-band{
  position:absolute;left:0;right:0;bottom:0;height:54px;
  background:linear-gradient(90deg,var(--brand-deep),var(--brand-light));
  color:#fff;font-size:15px;letter-spacing:1.5px;
  display:flex;align-items:center;justify-content:center;
}
/* back */
.mist-disc{
  position:absolute;left:150px;top:22px;width:280px;height:280px;border-radius:50%;
  background:var(--brand-mist);
}
.back-title{
  position:absolute;left:0;right:0;top:100px;text-align:center;
  font-size:36px;font-weight:600;color:var(--brand);letter-spacing:.3px;
}
.tagline{
  position:absolute;left:0;right:0;top:160px;text-align:center;
  font-style:italic;font-size:16px;line-height:1.5;color:var(--ink-soft);
}
</style>
</head>
<body>

<section class="card card-front" aria-label="Business card front">
  <div class="brand-disc"></div>
  <div class="details">
    <p class="person-name">Mark Holloway</p>
    <p class="person-role">Director</p>
    <div class="divider"></div>
    <p class="company-name">Kestrel Office Clearance</p>
    <address class="address">Unit K4 B, 2-8 Fenwick Lane<br>Ashcombe, Northfield Vale, ZZ9 4QT</address>
    <ul class="contact">
      <li>
        <svg viewBox="0 0 12 12" aria-hidden="true"><path d="M2.5 1h2l1 2.6-1.3.9a6.5 6.5 0 0 0 3.3 3.3l.9-1.3 2.6 1v2a1 1 0 0 1-1 1A9.5 9.5 0 0 1 1.5 2a1 1 0 0 1 1-1z" fill="var(--brand)"/></svg>
        01632 960418
      </li>
      <li>
        <svg viewBox="0 0 12 12" aria-hidden="true"><rect x="3" y="0.8" width="6" height="10.4" rx="1" fill="none" stroke="var(--brand)" stroke-width="1.3"/><circle cx="6" cy="9.3" r=".7" fill="var(--brand)"/></svg>
        07700 153928
      </li>
      <li>
        <svg viewBox="0 0 12 12" aria-hidden="true"><rect x="0.5" y="0.5" width="11" height="11" rx="1.5" fill="var(--brand)"/><path d="M3 6.2l2 2 4-4.4" fill="none" stroke="#fff" stroke-width="1.4"/></svg>
        mark@kestrelofficeclearance.co.uk
      </li>
    </ul>
  </div>
  <div class="web-band">www.kestrelofficeclearance.co.uk</div>
</section>

<section class="card card-back" aria-label="Business card back">
  <div class="mist-disc"></div>
  <h1 class="back-title">Kestrel Office Clearance</h1>
  <p class="tagline">Clear offices, fresh starts...<br>we leave only the space.</p>
</section>

</body>
</html>
```